Agriculture farming Hemp and CBD

The logo is in works with your company now, should be ready in a few days. We have our Domain (kestrelbrookhollow.com) We would like to see incorporated seed to growth, but not necessary. we would like to nature colors and some black and green. we have our farm and will be growing and selling HEMP and CBD we are based in the state of Virginia. Would like to incorporate the words pause, play, rewind if possible but not necessary.

Target Market(s)

20 years old to elderly

Coding

Coded - Design and coding required

Number of Pages Required

3 page

Font styles to use
Serif

Requirements
Must have
• I'm not sure on the must haves, we are open to any ideas, we would definitely like to see Hemp and CBD included, may the life cycle of seed to plant. We must have a pop up asking if you are 20 years old before they can enter our site and to view or purchase our product. I want the design to be totally different than what i uploaded.
Nice to have
• Would like to see natural colors as well as black and green
Should not have
• I want

```html
<!DOCTYPE html>
<html lang="en">
<head>
<meta charset="utf-8">
<title>Kestrel Brook Hollow – Hemp &amp; CBD</title>
<link href="https://fonts.googleapis.com/css2?family=Russo+One&family=Rajdhani:wght@700&family=Open+Sans:wght@400;600&family=Montserrat:wght@400;500;700&family=Kaushan+Script&family=Roboto+Condensed:wght@400&display=swap" rel="stylesheet">
<style>
:root{
  --green:#0a9a2c;
  --lime:#1fd51f;
  --black:#000;
  --ink:#111;
  --muted:#8a8a8a;
  --soft:#f8f8f8;
  --line:#e4e4e4;
  --white:#fff;
}
*{margin:0;padding:0;box-sizing:border-box}
html,body{width:1200px;height:3015px;overflow:hidden;background:var(--white)}
body{position:relative;font-family:"Open Sans",sans-serif;color:var(--ink)}
.abs{position:absolute}
.center{left:0;width:1200px;text-align:center}

/* header */
.topbar{left:0;top:0;width:1200px;height:37px;background:var(--black)}
.navbar{left:0;top:37px;width:1200px;height:47px;background:var(--green)}
.header-underline{left:0;top:82px;width:1200px;height:8px;background:var(--green)}
.logo-panel{left:0;top:0}
.brand{font-family:"Montserrat",sans-serif;font-weight:700;color:var(--black);font-size:29px;letter-spacing:-.5px}
.brand-head{left:162px;top:22px}
.phone{left:888px;top:10px;font-size:11px;color:var(--white);display:flex;align-items:center;gap:8px}
.phone b{color:var(--lime);font-weight:400}
.nav{top:55px;display:flex;font-family:"Open Sans",sans-serif;font-size:11px;color:var(--white);letter-spacing:.3px}
.nav span{position:absolute;white-space:nowrap}

/* hero */
.hero-photo{left:0;top:90px}
.hero-title{top:258px;font-family:"Russo One",sans-serif;font-size:52px;line-height:57px;color:var(--white);letter-spacing:1px;text-shadow:0 3px 4px rgba(0,0,0,.45)}
.hero-title em{font-style:normal;color:var(--lime)}
.hero-sub{top:386px;font-size:14px;line-height:23px;color:var(--white)}
.btn{font-family:"Roboto Condensed",sans-serif;font-size:14px;color:var(--white);display:flex;align-items:center;justify-content:center}
.btn-learn{left:465px;top:458px;width:126px;height:44px;background:var(--green)}
.btn-contact{left:608px;top:458px;width:126px;height:44px;background:var(--lime)}

.marker-line{width:2px;background:var(--green);left:599px}
.marker{width:44px;height:44px;border-radius:50%;background:var(--green);left:578px}

/* about */
.eyebrow{top:806px;font-family:"Kaushan Script",cursive;color:var(--green);font-size:19px}
.section-title{font-family:"Rajdhani",sans-serif;font-weight:700;font-size:34px;letter-spacing:.5px;color:var(--ink)}
.about-title{top:838px}
.about-copy{left:331px;top:889px;width:538px;text-align:center;font-size:11px;line-height:19px;color:var(--muted)}
.cycle{left:0;top:990px}
.stage{font-family:"Montserrat",sans-serif}
.stage h4{font-weight:400;font-size:13px;color:var(--ink);margin-bottom:6px}
.stage p{font-family:"Open Sans",sans-serif;font-size:11px;line-height:16px;color:var(--muted)}
.stage.right{text-align:right}

/* products */
.products-band{left:0;top:1469px;width:1200px;height:562px;background:var(--soft)}
.products-title{top:1526px}
.card{width:202px;height:201px;background:#f1f1f1;border:1px solid #e6e6e6;top:1605px}
.card .inner{position:absolute;left:19px;top:19px;width:162px;height:162px;background:var(--white)}
.heart{position:absolute;width:21px;height:21px;border-radius:50%;right:8px;top:8px;display:flex;align-items:center;justify-content:center}
.heart.on{background:var(--lime);width:30px;height:30px;right:6px;top:6px}
.pinfo{top:1828px;width:202px;text-align:center}
.pinfo h5{font-family:"Montserrat",sans-serif;font-weight:400;font-size:15px;color:var(--green)}
.pinfo p{font-size:11px;line-height:19px;color:var(--muted);margin-top:6px}
.pinfo .price{font-family:"Montserrat",sans-serif;font-size:15px;color:var(--ink);margin-top:12px}
.cart{margin:12px auto 0;width:105px;height:30px;border:1px solid var(--green);color:var(--green);font-family:"Roboto Condensed",sans-serif;font-size:11px;display:flex;align-items:center;justify-content:center}
.cart.on{background:var(--green);color:var(--white)}
.arrow{width:30px;height:30px;border:1px solid #ddd;background:var(--white);display:flex;align-items:center;justify-content:center;top:1692px}

/* blog */
.blog-title{top:2089px}
.post-photo{top:2160px;width:270px;height:180px}
.post{top:2367px;width:270px}
.date{display:inline-block;background:var(--green);color:var(--white);font-family:"Roboto Condensed",sans-serif;font-size:10px;padding:4px 13px}
.post h6{font-family:"Montserrat",sans-serif;font-weight:500;font-size:13px;margin:24px 0 0 1px}
.post p{font-family:"Montserrat",sans-serif;font-size:11px;line-height:19px;color:var(--muted);margin:8px 0 0 1px}
.post a{display:block;margin:10px 0 0 1px;font-family:"Roboto Condensed",sans-serif;font-size:10px;color:var(--green);text-decoration:underline}

/* footer */
.footer-shape{left:0;top:2587px}
.brand-foot{top:2728px;color:var(--white);font-size:27px}
.contact-line{top:2788px;font-size:14px;color:var(--white)}
.contact-line b{font-weight:400;color:var(--lime)}
.foot-links{top:2830px;font-size:11px;color:#ddd;word-spacing:2px}
.social{top:2870px;width:34px;height:33px;background:var(--green)}
.copyright-band{left:0;top:2964px;width:1200px;height:51px;background:var(--green)}
.copyright{top:2983px;font-size:11px;color:var(--white)}
</style>
</head>
<body>

<!-- header -->
<div class="abs topbar"></div>
<div class="abs navbar"></div>
<div class="abs header-underline"></div>
<svg class="abs logo-panel" width="540" height="84" aria-hidden="true"><polygon points="0,0 539,0 510,84 0,84" fill="#fff"/></svg>
<div class="abs brand brand-head">kestrelbrookhollow.com</div>

<div class="abs phone">
  <svg width="16" height="16" viewBox="0 0 24 24" fill="none" stroke="#1fd51f" stroke-width="1.6"><path d="M5 3h4l2 5-2.5 1.5a11 11 0 0 0 6 6L16 13l5 2v4a2 2 0 0 1-2 2A17 17 0 0 1 3 5a2 2 0 0 1 2-2z"/></svg>
  <span><b>Phone&nbsp; :</b>&nbsp; 123.456.7890</span>
</div>
<div class="abs nav">
  <span style="left:652px">HOME</span>
  <span style="left:712px">OUR STORY</span>
  <span style="left:802px">PRODUCTS</span>
  <span style="left:889px">BLOG</span>
  <span style="left:948px">CONTACT</span>
</div>
<svg class="abs" style="left:1024px;top:56px" width="15" height="15" viewBox="0 0 16 16" fill="none" stroke="#fff" stroke-width="1.5"><circle cx="6.5" cy="6.5" r="5"/><line x1="10.3" y1="10.3" x2="15" y2="15"/></svg>

<!-- hero -->
<svg class="abs hero-photo" width="1200" height="640" role="img" aria-label="Photo of a grower lifting a potted hemp plant in a greenhouse">
  <defs>
    <linearGradient id="heroTone" x1="0" y1="0" x2="1" y2="1">
      <stop offset="0" stop-color="#4c5a3a"/>
      <stop offset=".45" stop-color="#2f3a26"/>
      <stop offset="1" stop-color="#3d4d2c"/>
    </linearGradient>
  </defs>
  <polygon points="0,0 1200,0 1200,562 314,637 0,510" fill="url(#heroTone)"/>
</svg>
<div class="abs center hero-title"><em>ROOTED IN</em> CULTURE<br>HEMP <em>CBD OIL</em></div>
<div class="abs center hero-sub">we have our farm and will be growing and selling HEMP and CBD<br>we are based in the state of Virginia.</div>
<div class="abs btn btn-learn">LEARN MORE</div>
<div class="abs btn btn-contact">CONTACT US</div>

<div class="abs marker-line" style="top:703px;height:32px"></div>
<div class="abs marker" style="top:734px"></div>

<!-- about -->
<div class="abs center eyebrow">Our History</div>
<div class="abs center section-title about-title">ABOUT COMPANY</div>
<p class="abs about-copy">Lorem ipsum dolor sit amet, consectetur adipiscing elit, sed do eiusmod tempor incididunt ut labore et dolore magna aliqua. Ut enim ad minim veniam, quis nostrud exercitation ullamco laboris nisi ut aliquip ex ea commodo consequat. Duis aute irure dolor in reprehenderit in voluptate velit esse cillum dolore eu fugiat nulla pariatur. Excepteur sint occaecat cupidatat non proident.</p>

<svg class="abs cycle" width="1200" height="340">
  <path d="M432 75 A184 184 0 1 0 766 75" fill="none" stroke="#d8d8d8" stroke-width="1.2" stroke-dasharray="3 3" transform="translate(0,0)"/>
  <circle cx="432" cy="75" r="7" fill="#fff" stroke="#0a9a2c" stroke-width="1.5"/><circle cx="432" cy="75" r="3.5" fill="#0a9a2c"/>
  <circle cx="766" cy="75" r="7" fill="#fff" stroke="#0a9a2c" stroke-width="1.5"/><circle cx="766" cy="75" r="3.5" fill="#0a9a2c"/>
  <g role="img" aria-label="Photo of a wooden bowl filled with fresh hemp leaves">
    <circle cx="600" cy="140" r="127" fill="#b57a3c"/>
    <circle cx="600" cy="140" r="110" fill="#4f9a2c"/>
  </g>
  <g fill="#fff" stroke="#eee">
    <circle cx="419" cy="178" r="33"/><circle cx="480" cy="278" r="33"/><circle cx="600" cy="319" r="33"/><circle cx="718" cy="278" r="33"/><circle cx="779" cy="178" r="33"/>
  </g>
  <circle cx="419" cy="178" r="14" fill="#8a7352" role="img" aria-label="Hemp seeds"/>
  <circle cx="480" cy="278" r="13" fill="#5fa83a" role="img" aria-label="Seedling"/>
  <circle cx="600" cy="319" r="14" fill="#4f8f30" role="img" aria-label="Young hemp plant"/>
  <circle cx="718" cy="278" r="14" fill="#3f6a2a" role="img" aria-label="Hemp hanging to dry"/>
  <circle cx="779" cy="178" r="14" fill="#3d7a2a" role="img" aria-label="Processed hemp flower"/>
</svg>
<div class="abs stage right" style="left:200px;top:1140px;width:158px"><h4>SEED</h4><p>We start with the best<br>seed genetics</p></div>
<div class="abs stage right" style="left:240px;top:1241px;width:178px"><h4>NURSERY</h4><p>Grow healthy plants in our<br>greenhouse</p></div>
<div class="abs stage" style="left:837px;top:1140px;width:180px"><h4>FRUIT</h4><p>Process material to<br>usable forms</p></div>
<div class="abs stage" style="left:778px;top:1237px;width:180px"><h4>HARVEST</h4><p>Harvest and dry in<br>good conditions</p></div>
<div class="abs stage center" style="top:1368px"><h4>FULL PLANTS</h4><p>Move plants outdoors in the sunshine</p></div>

<!-- products -->
<div class="abs products-band"></div>
<div class="abs center section-title products-title">OUR PRODUCTS</div>

<div class="abs arrow" style="left:116px"><svg width="8" height="12" viewBox="0 0 8 12" fill="none" stroke="#333" stroke-width="1.4"><path d="M6 1L1 6l5 5"/></svg></div>
<div class="abs arrow" style="left:1054px"><svg width="8" height="12" viewBox="0 0 8 12" fill="none" stroke="#333" stroke-width="1.4"><path d="M2 1l5 5-5 5"/></svg></div>

<div class="abs card" style="left:162px"><div class="inner"><svg style="position:absolute;left:51px;top:44px" width="60" height="80" role="img" aria-label="CBD oil bottle with green box"><rect x="22" y="4" width="34" height="72" fill="#5fb84a"/><rect x="4" y="30" width="22" height="46" rx="3" fill="#2e3a24"/></svg><div class="heart on"><svg width="13" height="12" viewBox="0 0 24 22" fill="#fff"><path d="M12 21L2 11a5.5 5.5 0 0 1 10-7 5.5 5.5 0 0 1 10 7z"/></svg></div></div></div>
<div class="abs card" style="left:386px"><div class="inner"><svg style="position:absolute;left:51px;top:44px" width="60" height="80" role="img" aria-label="Cannabis oil bottle with black and gold box"><rect x="22" y="4" width="34" height="72" fill="#222"/><rect x="4" y="30" width="22" height="46" rx="3" fill="#7a4a12"/></svg><div class="heart"><svg width="13" height="12" viewBox="0 0 24 22" fill="#1fd51f"><path d="M12 21L2 11a5.5 5.5 0 0 1 10-7 5.5 5.5 0 0 1 10 7z"/></svg></div></div></div>
<div class="abs card" style="left:611px"><div class="inner"><svg style="position:absolute;left:51px;top:44px" width="60" height="80" role="img" aria-label="CBD oil bottle with green box"><rect x="22" y="4" width="34" height="72" fill="#5fb84a"/><rect x="4" y="30" width="22" height="46" rx="3" fill="#2e3a24"/></svg><div class="heart"><svg width="13" height="12" viewBox="0 0 24 22" fill="#1fd51f"><path d="M12 21L2 11a5.5 5.5 0 0 1 10-7 5.5 5.5 0 0 1 10 7z"/></svg></div></div></div>
<div class="abs card" style="left:836px"><div class="inner"><svg style="position:absolute;left:51px;top:44px" width="60" height="80" role="img" aria-label="Cannabis oil bottle with black and gold box"><rect x="22" y="4" width="34" height="72" fill="#222"/><rect x="4" y="30" width="22" height="46" rx="3" fill="#7a4a12"/></svg><div class="heart"><svg width="13" height="12" viewBox="0 0 24 22" fill="#1fd51f"><path d="M12 21L2 11a5.5 5.5 0 0 1 10-7 5.5 5.5 0 0 1 10 7z"/></svg></div></div></div>

<div class="abs pinfo" style="left:160px"><h5>Product Name</h5><p>Lorem ipsum dolor sit amet,<br>consectetur adipiscing.</p><div class="price">$00.00</div><div class="cart on">ADD TO CART</div></div>
<div class="abs pinfo" style="left:385px"><h5>Product Name</h5><p>Lorem ipsum dolor sit amet,<br>consectetur adipiscing.</p><div class="price">$00.00</div><div class="cart">ADD TO CART</div></div>
<div class="abs pinfo" style="left:610px"><h5>Product Name</h5><p>Lorem ipsum dolor sit amet,<br>consectetur adipiscing.</p><div class="price">$00.00</div><div class="cart">ADD TO CART</div></div>
<div class="abs pinfo" style="left:836px"><h5>Product Name</h5><p>Lorem ipsum dolor sit amet,<br>consectetur adipiscing.</p><div class="price">$00.00</div><div class="cart">ADD TO CART</div></div>

<!-- blog -->
<div class="abs center section-title blog-title">RECENT BLOG</div>
<div class="abs post-photo" style="left:162px;background:linear-gradient(135deg,#4a5a30,#2c3a1e)" role="img" aria-label="Photo of a farmer harvesting tall hemp stalks in a field"></div>
<div class="abs post-photo" style="left:465px;background:linear-gradient(135deg,#5c6a3e,#8a8a78)" role="img" aria-label="Photo of a hemp leaf and dried flower on a grey surface"></div>
<div class="abs post-photo" style="left:768px;background:linear-gradient(135deg,#9aa88a,#3e5a2c)" role="img" aria-label="Photo of a gloved hand holding a hemp seedling"></div>

<div class="abs post" style="left:162px"><span class="date">2 Sep 2020</span><h6>Lorem ipsum dolor</h6><p>Lorem ipsum dolor sit amet, consect adipisc ing elit, sed do eiusmod tempor incididunt ut labore et dolore magna aliqua.</p><a>LEARN MORE</a></div>
<div class="abs post" style="left:465px"><span class="date">2 Sep 2020</span><h6>Lorem ipsum dolor</h6><p>Lorem ipsum dolor sit amet, consect adipisc ing elit, sed do eiusmod tempor incididunt ut labore et dolore magna aliqua.</p><a>LEARN MORE</a></div>
<div class="abs post" style="left:768px"><span class="date">2 Sep 2020</span><h6>Lorem ipsum dolor</h6><p>Lorem ipsum dolor sit amet, consect adipisc ing elit, sed do eiusmod tempor incididunt ut labore et dolore magna aliqua.</p><a>LEARN MORE</a></div>

<!-- footer -->
<svg class="abs footer-shape" width="1200" height="428" aria-hidden="true"><polygon points="0,76 884,0 1200,129 1200,428 0,428" fill="#000"/></svg>
<div class="abs marker-line" style="top:2613px;height:36px"></div>
<div class="abs marker" style="top:2648px"></div>
<div class="abs center brand brand-foot">kestrelbrookhollow.com</div>
<div class="abs center contact-line"><b>Email</b>&nbsp; : &nbsp;hello@kestrelbrookhollow.com &nbsp;&nbsp;&nbsp;|&nbsp;&nbsp;&nbsp; <b>Phone</b>&nbsp; : &nbsp;123.456.7890</div>
<div class="abs center foot-links">Home &nbsp;&nbsp;|&nbsp;&nbsp; Our Story &nbsp;&nbsp;|&nbsp;&nbsp; Products &nbsp;&nbsp;|&nbsp;&nbsp; Blog &nbsp;&nbsp;|&nbsp;&nbsp; Contact</div>
<div class="abs social" style="left:542px" aria-label="Social link"></div>
<div class="abs social" style="left:583px" aria-label="Social link"></div>
<div class="abs social" style="left:624px" aria-label="Social link"></div>
<div class="abs copyright-band"></div>
<div class="abs center copyright">© 2020 kestrelbrookhollow.com - &nbsp;All Rights Reserved</div>

</body>
</html>
```